Letterhead for a German Distribution/Manufacturing Company

We need a professional Letterhead in a unique Design.
not to playful.
The Letterhead has to show show that we are a international company with headquater in Germany.
all details like adress, Vat Tax Number, Bank Accout, Eori, email, Company number has to be on the Letterhead.
for example use: VAT TAX DE5470318 Bank Account: Kestrel Bank IBAN DE412058731ß204683 Swift: MORV0417352 EORI 3150428697 Company Number: HRB 51806 Adress: VOLMINTA UG Ahornweg 7 Postal Code 06384 City Kerbstadt Country: Germany Email: info@volminta-example.com
the design can be colored but doesnt have to be
Industry/Entity Type
Manufacturing and international distribution
Requirements
Must have
- show that we are a international company with headquater in Germany. our company infos and logo

```html
<!DOCTYPE html>
<html lang="en">
<head>
<meta charset="utf-8">
<title>VOLMINTA UG – Letterhead</title>
<link rel="stylesheet" href="https://fonts.googleapis.com/css2?family=Open+Sans:wght@400&family=Roboto:wght@400;500;700&family=Montserrat:wght@400&display=swap">
<style>
  :root {
    --backdrop: #dcdcdc;
    --paper: #f7f7f7;
    --ink-strong: #444446;
    --ink-body: #5f5f61;
    --band-light: #707074;
    --band-dark: #444446;
    --signature-ink: #1c2541;
  }
  * { box-sizing: border-box; margin: 0; padding: 0; }
  html, body {
    width: 1153px;
    height: 1200px;
    overflow: hidden;
    background: var(--backdrop);
  }
  .letterhead {
    position: absolute;
    left: 163px;
    top: 24px;
    width: 827px;
    height: 1153px;
    background: var(--paper);
    overflow: hidden;
  }
  .brand {
    position: absolute;
    left: 82px;
    top: 70px;
    display: flex;
    align-items: center;
    gap: 18px;
  }
  .brand-dot {
    width: 72px;
    height: 72px;
    border-radius: 50%;
    background: var(--ink-strong);
  }
  .brand-name {
    font-family: "Montserrat", sans-serif;
    font-weight: 400;
    font-size: 48px;
    letter-spacing: 1px;
    color: var(--ink-strong);
  }
  .sender {
    position: absolute;
    left: 584px;
    top: 60px;
    font-family: "Roboto", sans-serif;
    font-style: normal;
    font-size: 14px;
    line-height: 17.5px;
    color: var(--ink-strong);
  }
  .sender-contacts { margin-top: 6px; list-style: none; }
  .sender-contacts li {
    display: flex;
    align-items: center;
    gap: 6px;
    line-height: 19px;
  }
  .sender-contacts svg { width: 14px; height: 12px; fill: var(--ink-strong); }
  .letter-body {
    position: absolute;
    left: 82px;
    top: 285px;
    width: 663px;
    font-family: "Open Sans", sans-serif;
    font-size: 15.2px;
    line-height: 21.7px;
    color: var(--ink-body);
  }
  .letter-body p { margin-bottom: 21.8px; text-align: justify; text-align-last: left; }
  .signature {
    position: absolute;
    left: 82px;
    top: 858px;
    width: 94px;
    height: 88px;
    background: radial-gradient(ellipse at center, rgba(28,37,65,0.18), rgba(28,37,65,0) 70%);
  }
  .company-register {
    position: absolute;
    left: 82px;
    top: 1053px;
    font-family: "Roboto", sans-serif;
    font-size: 14px;
    line-height: 19.7px;
    color: var(--ink-strong);
  }
  .company-register .divider { font-weight: 700; margin: 0 4px; }
  .footer-band {
    position: absolute;
    left: 0;
    bottom: 0;
    width: 827px;
    height: 30px;
  }
  .band-light { fill: var(--band-light); }
  .band-dark { fill: var(--band-dark); }
  .website {
    font-family: "Roboto", sans-serif;
    font-weight: 500;
    font-size: 15px;
    fill: #ffffff;
  }
</style>
</head>
<body>
<main class="letterhead">
  <header>
    <div class="brand">
      <span class="brand-dot"></span>
      <span class="brand-name">VOLMINTA</span>
    </div>
    <address class="sender">
      VOLMINTA UG<br>
      Ahornweg 7 06384<br>
      City Kerbstadt Germany
      <ul class="sender-contacts">
        <li>
          <svg viewBox="0 0 14 12" aria-hidden="true"><path d="M1 4 C1 1 13 1 13 4 L10.5 4.6 L9.8 3 C8 2.5 6 2.5 4.2 3 L3.5 4.6 Z M4.5 5 H9.5 L12 11 H2 Z"/></svg>
          541.306.2279
        </li>
        <li>
          <svg viewBox="0 0 14 12" aria-hidden="true"><path d="M1 2 H13 V3 L7 7 L1 3 Z M1 4.4 L7 8.4 L13 4.4 V10 H1 Z"/></svg>
          info@volminta-example.com
        </li>
      </ul>
    </address>
  </header>

  <section class="letter-body">
    <p>Dear customer,</p>
    <p>Lorem ipsum dolor sit amet, consectetur adipisicing elit, sed do eiusmod tempor incididunt ut labore et dolore magna aliqua. Ut enim ad minim veniam, quis nostrud exercitation ullamco laboris nisi ut aliquip ex ea commodo consequat. Duis aute irure dolor in reprehenderit in voluptate velit esse cillum dolore eu fugiat nulla pariatur. Excepteur sint occaecat cupidatat non proident, sunt in culpa qui officia deserunt mollit anim id est laborum.</p>
    <p>Lorem ipsum dolor sit amet, consectetur adipisicing elit, sed do eiusmod tempor incididunt ut labore et dolore magna aliqua. Ut enim ad minim veniam, quis nostrud exercitation ullamco laboris nisi ut aliquip ex ea commodo consequat. Duis aute irure dolor in reprehenderit in voluptate velit esse cillum dolore eu fugiat nulla pariatur. Excepteur sint occaecat cupidatat non proident, sunt in culpa qui officia deserunt mollit anim id est laborum.</p>
    <p>Lorem ipsum dolor sit amet, consectetur adipisicing elit, sed do eiusmod tempor incididunt ut labore et dolore magna aliqua. Ut enim ad minim veniam, quis nostrud exercitation ullamco laboris nisi ut aliquip ex ea commodo consequat. Duis aute irure dolor in reprehenderit in voluptate velit esse cillum dolore eu fugiat nulla pariatur. Excepteur sint occaecat cupidatat non proident, sunt in culpa qui officia deserunt mollit anim id est laborum.</p>
    <p>Lorem ipsum dolor sit amet, consectetur adipisicing elit, sed do eiusmod tempor incididunt ut labore et dolore magna aliqua. Ut enim ad minim veniam, quis nostrud exercitation ullamco laboris nisi ut aliquip ex ea commodo consequat. Duis aute irure dolor in reprehenderit.</p>
    <p>Yours Sincerely,</p>
  </section>

  <div class="signature" role="img" aria-label="Handwritten signature"></div>

  <footer>
    <div class="company-register">
      VAT TAX DE5470318<br>
      Bank Account: Kestrel Bank IBAN DE412058731ß204683<br>
      Swift: MORV0417352 EORI 3150428697<span class="divider">|</span>Company Number: HRB 51806
    </div>
    <svg class="footer-band" viewBox="0 0 827 30">
      <polygon class="band-light" points="0,12 583,12 565,30 0,30"/>
      <polygon class="band-dark" points="596,0 827,0 827,30 572,30"/>
      <text class="website" x="694" y="20" text-anchor="middle">www.volminta-example.com</text>
    </svg>
  </footer>
</main>
</body>
</html>
```